BOLD & MINIMALIST DESIGN NEEDED

We want a very bold but minimalistic business card design that is impactful and utilizes both sides of the business card. Our current logo is included for your use.

We want bold fonts and good use of negative space. We don't want the logo to overpower the design.

Target Market(s)

Professionals who are building new commercial buildings.

Industry/Entity Type

Construction

Contact Information for Business Card

Name, Title, email, office phone, cell phone, website

Font styles to use
Serif
Sans Serif

Requirements
Must have
• Bold design!

```html
<!DOCTYPE html>
<html lang="en">
<head>
<meta charset="utf-8">
<title>Ridgeway Design + Build — Business Card</title>
<link href="https://fonts.googleapis.com/css2?family=Poppins:wght@400;600;700;800&display=swap" rel="stylesheet">
<style>
  :root {
    --backdrop: #202020;
    --card-dark: #0e0e0e;
    --card-light: #ffffff;
    --ink: #111111;
    --accent: #7cc242;
    --paper-text: #ffffff;
  }
  * { box-sizing: border-box; margin: 0; padding: 0; }
  html, body {
    width: 1200px; height: 1200px; overflow: hidden;
    background: var(--backdrop);
    font-family: "Poppins", sans-serif;
  }
  .canvas {
    position: relative; width: 1200px; height: 1200px;
    display: flex; flex-direction: column; align-items: center; justify-content: center;
    gap: 44px;
  }
  .card {
    width: 880px; height: 503px; position: relative;
    box-shadow: 0 14px 30px rgba(0,0,0,.45);
  }
  .card--front { background: var(--card-dark); color: var(--paper-text);
    display: flex; flex-direction: column; align-items: center; justify-content: center; gap: 48px; }
  .card--back { background: var(--card-light); color: var(--ink); }

  .brand { display: flex; align-items: center; gap: 20px; }
  .brand__mark { width: 34px; height: 34px; background: var(--accent); flex: none; }
  .brand__name {
    font-weight: 800; font-size: 46px; line-height: 1.05; letter-spacing: .5px; text-transform: uppercase;
  }
  .card--front .brand__name { color: var(--paper-text); }
  .card--back .brand__name { color: var(--ink); font-size: 40px; }

  .website {
    font-size: 24px; font-weight: 400; letter-spacing: 10px; color: var(--paper-text);
  }

  .card--back .brand { position: absolute; left: 56px; top: 200px; }

  .contact { position: absolute; left: 470px; top: 140px; }
  .contact__head { border-left: 4px solid var(--accent); padding-left: 22px; margin-bottom: 34px; }
  .contact__name { font-weight: 700; font-size: 34px; letter-spacing: 1px; line-height: 1.1; }
  .contact__title { color: var(--accent); font-size: 23px; font-weight: 400; }
  .contact__address { font-size: 23px; line-height: 1.35; margin-bottom: 14px; }
  .contact__row { display: flex; align-items: center; gap: 14px; font-size: 25px; line-height: 1.45; }
  .contact__icon { width: 20px; height: 20px; flex: none; }
</style>
</head>
<body>
<main class="canvas">
  <section class="card card--front" aria-label="Card front">
    <div class="brand">
      <span class="brand__mark"></span>
      <span class="brand__name">Ridgeway<br>Design + Build</span>
    </div>
    <p class="website">www.ridgewaybuild.com</p>
  </section>

  <section class="card card--back" aria-label="Card back">
    <div class="brand">
      <span class="brand__mark"></span>
      <span class="brand__name">Ridgeway<br>Design + Build</span>
    </div>
    <div class="contact">
      <div class="contact__head">
        <p class="contact__name">OWEN HARPER</p>
        <p class="contact__title">Craftsman</p>
      </div>
      <p class="contact__address">PO BOX 48 Harbour Lane<br>Level 2 Quarry Road</p>
      <p class="contact__row">
        <svg class="contact__icon" viewBox="0 0 24 24" aria-hidden="true"><path fill="#7cc242" d="M6.6 10.8a15.1 15.1 0 0 0 6.6 6.6l2.2-2.2c.3-.3.7-.4 1-.2 1.1.4 2.3.6 3.6.6.6 0 1 .4 1 1V20c0 .6-.4 1-1 1A17 17 0 0 1 3 4c0-.6.4-1 1-1h3.5c.6 0 1 .4 1 1 0 1.3.2 2.5.6 3.6.1.3 0 .7-.2 1z"/></svg>
        (555) 013-2468
      </p>
      <p class="contact__row">
        <svg class="contact__icon" viewBox="0 0 24 24" aria-hidden="true"><rect x="2" y="5" width="20" height="14" fill="#7cc242"/><path d="M2 5l10 8 10-8" fill="none" stroke="#ffffff" stroke-width="1.6"/></svg>
        info@ridgewaybuild.com.au
      </p>
    </div>
  </section>
</main>
</body>
</html>
```